Construction Company

Design a clutter free business card, it can be double-sided utilizing the logo for VKM Ltd simple with all relevant contact information.

Please also a letterhead design to function for the purposes of invoicing, all mail requirements, with header to be distinctive while the footer ties page together and incorporates all necessary information.

For now, please use generic / dummy text and when a winner is selected, I will disclose the contact information.

Hi Designers! Please read the updated brief which includes the design of a business card and letterhead. Thank you!

```html
<!DOCTYPE html>
<html lang="en">
<head>
<meta charset="utf-8">
<title>VKM Ltd — Business Card</title>
<link rel="stylesheet" href="https://fonts.googleapis.com/css2?family=Open+Sans:ital,wght@0,400;0,700;1,400&display=swap">
<style>
  :root {
    --card-blue: #263a88;
    --accent-gold: #b8902f;
    --text-white: #ffffff;
    --backdrop: #1c1c1e;
  }
  * { box-sizing: border-box; margin: 0; padding: 0; }
  html, body {
    width: 1200px;
    height: 900px;
    overflow: hidden;
    background: var(--backdrop);
    font-family: "Open Sans", Arial, sans-serif;
  }
  .canvas {
    width: 1200px;
    height: 900px;
    display: flex;
    flex-direction: column;
    align-items: center;
    justify-content: center;
    gap: 40px;
  }
  .card {
    width: 700px;
    height: 400px;
    background: var(--card-blue);
    position: relative;
  }
  /* Front */
  .card-front {
    display: flex;
    align-items: center;
    padding: 0 60px 0 70px;
  }
  .brand-name {
    width: 250px;
    color: var(--text-white);
    font-size: 52px;
    font-weight: 700;
    letter-spacing: 1px;
  }
  .divider {
    width: 2px;
    height: 200px;
    background: var(--accent-gold);
    margin: 0 34px 0 20px;
  }
  .contact {
    color: var(--text-white);
    font-size: 17px;
    line-height: 1.45;
  }
  .contact-name {
    color: var(--accent-gold);
    font-weight: 700;
    font-size: 20px;
    text-transform: uppercase;
    letter-spacing: 0.5px;
  }
  .contact-role { margin-bottom: 2px; }
  .contact-line {
    display: flex;
    align-items: center;
    gap: 8px;
  }
  .contact-line svg {
    width: 13px;
    height: 13px;
    flex: none;
    fill: var(--accent-gold);
  }
  /* Back */
  .card-back {
    display: flex;
    align-items: center;
    justify-content: center;
    gap: 18px;
  }
  .back-mark {
    width: 22px;
    height: 22px;
    border-radius: 50%;
    background: var(--accent-gold);
  }
  .back-name {
    color: var(--accent-gold);
    font-size: 44px;
    font-weight: 700;
    letter-spacing: 1px;
  }
</style>
</head>
<body>
  <main class="canvas">
    <section class="card card-front">
      <div class="brand-name">VKM Ltd</div>
      <div class="divider"></div>
      <div class="contact">
        <p class="contact-name">Daniel Harrow</p>
        <p class="contact-role">President</p>
        <p>1820 Harbor View Road</p>
        <p>Lakeside CA 90417</p>
        <p class="contact-line">
          <svg viewBox="0 0 24 24" aria-hidden="true"><path d="M6.6 10.8a15.1 15.1 0 0 0 6.6 6.6l2.2-2.2a1 1 0 0 1 1-.25 11.4 11.4 0 0 0 3.6.57 1 1 0 0 1 1 1V20a1 1 0 0 1-1 1A17 17 0 0 1 3 4a1 1 0 0 1 1-1h3.5a1 1 0 0 1 1 1c0 1.25.2 2.45.57 3.6a1 1 0 0 1-.25 1z"/></svg>
          555-310-4827
        </p>
        <p class="contact-line">
          <svg viewBox="0 0 24 24" aria-hidden="true"><path d="M2 5h20v14H2z" fill="none"/><path d="M2 5h20v2l-10 6L2 7zm0 4 10 6 10-6v10H2z"/></svg>
          dharrow@vkmltd.com
        </p>
        <p class="contact-line">
          <svg viewBox="0 0 24 24" aria-hidden="true"><circle cx="12" cy="12" r="10"/></svg>
          www.vkmltd.com
        </p>
      </div>
    </section>

    <section class="card card-back">
      <span class="back-mark"></span>
      <span class="back-name">VKM Ltd</span>
    </section>
  </main>
</body>
</html>
```